Quill Physical Therapy Website

I would need a clean modern website built to showcase my Physical therapy brand and services. I would need a simple but descriptive website that can ultimately connect my patients to my electronic medical portal so they may book an appointment..

```html
<!DOCTYPE html>
<html lang="en">
<head>
<meta charset="utf-8">
<title>Quill Physical Therapy</title>
<link href="https://fonts.googleapis.com/css2?family=Roboto:ital,wght@0,400;0,500;0,700;1,400&display=swap" rel="stylesheet">
<style>
:root{
  --teal:#137a78;
  --teal-dark:#0e5f5e;
  --green:#79c257;
  --green-head:#6ab94a;
  --blue:#4358a8;
  --ink:#222;
  --muted:#555;
  --black:#0b0b0b;
  --white:#fff;
}
*{box-sizing:border-box;margin:0;padding:0}
html,body{width:1200px;height:4602px;overflow:hidden}
body{position:relative;font-family:"Roboto",sans-serif;color:var(--ink);background:var(--white)}
.abs{position:absolute}
.center{text-align:center}
.para{font-size:13px;line-height:29px;color:var(--muted)}
.section-title{font-size:31px;font-weight:500;color:var(--green-head);text-transform:uppercase;letter-spacing:.2px}
.swoosh{display:block;margin:4px auto 0}
.btn{display:flex;align-items:center;justify-content:center;border-radius:30px;font-size:14px;font-weight:700;text-transform:uppercase;color:var(--white)}
/* header */
.site-header{left:0;top:0;width:1200px;height:86px;background:var(--white);z-index:5}
.logo-box{left:106px;top:0;width:172px;height:130px;background:var(--white);z-index:6;display:flex;flex-direction:column;align-items:center;justify-content:center;gap:6px}
.logo-dot{width:46px;height:46px;border-radius:50%;background:var(--teal)}
.logo-name{font-size:28px;font-weight:700;color:var(--teal);letter-spacing:1px}
.nav{left:314px;top:0;height:86px;display:flex;align-items:center;gap:28px;font-size:13px;font-weight:500;text-transform:uppercase;color:#333}
.nav-cta{left:846px;top:16px;width:222px;height:52px;background:var(--teal);font-size:15px}
/* hero */
.hero{left:0;top:86px;width:1200px;height:640px;background:linear-gradient(120deg,#8a8580 0%,#cfc9c2 40%,#e6e1db 70%,#b9b3ad 100%)}
.hero-shade{left:0;top:86px;width:1200px;height:640px;background:rgba(0,0,0,.28)}
.hero-title{left:0;top:280px;width:1200px;font-size:62px;font-weight:500;color:var(--white);text-transform:uppercase}
.hero-text{left:0;top:364px;width:1200px;font-size:14px;line-height:29px;color:var(--white)}
.hero-btn{left:490px;top:447px;width:221px;height:49px;background:var(--green)}
.dots{left:570px;top:655px;display:flex;gap:6px}
.dots span{width:12px;height:12px;border-radius:50%;border:1.5px solid var(--white)}
.dots span:first-child{background:var(--white)}
/* services */
.card{width:296px;height:348px;overflow:hidden}
.card-photo{width:100%;height:100%}
.card-band{position:absolute;left:0;bottom:0;width:100%;height:78px;display:flex;align-items:center;justify-content:center;color:var(--white);font-size:17px;font-weight:700;text-transform:uppercase}
.card-band.open{height:174px;flex-direction:column;justify-content:flex-start;padding-top:52px}
.card-band.open p{font-size:12px;font-weight:400;text-transform:none;line-height:28px;text-align:center;padding:4px 30px 0}
.card-icon{position:absolute;left:50%;top:-26px;width:54px;height:54px;margin-left:-27px;border-radius:50%;border:3px solid var(--white);background:inherit}
.teal{background:var(--teal)}.green{background:var(--green)}.blue{background:var(--blue)}
/* about */
.about{left:0;top:1782px;width:1200px;height:573px;background:linear-gradient(90deg,var(--teal-dark) 0%,var(--teal) 45%,#2d7f7d 100%)}
.about-title{left:77px;top:1856px;font-size:31px;font-weight:500;color:var(--white);line-height:40px;text-transform:uppercase}
.about-text{left:77px;top:1964px;width:430px;font-size:12px;line-height:28.5px;color:var(--white)}
.about-btn{left:77px;top:2209px;width:180px;height:49px;background:var(--green)}
/* testimonials */
.testimonials{left:0;top:2355px;width:1200px;height:424px;background:var(--green)}
.testi-title{left:0;top:2457px;width:1200px;color:var(--white);font-size:31px;font-weight:500}
.testi-text{left:210px;top:2534px;width:780px;font-size:12px;font-style:italic;line-height:28.5px;color:var(--white)}
.testi-name{left:0;top:2686px;width:1200px;font-size:16px;font-weight:700;color:var(--white)}
.arrow{width:54px;height:54px;border-radius:50%;background:var(--white);display:flex;align-items:center;justify-content:center}
/* blog */
.blog-card{width:300px}
.blog-photo{width:300px;height:201px}
.blog-card h3{font-size:16px;line-height:28px;font-weight:500;text-transform:uppercase;margin:14px 10px 4px}
.blog-card p{font-size:12px;line-height:28px;color:var(--muted);margin:0 10px}
.more{display:block;font-size:12px;font-weight:700;color:var(--teal);text-transform:uppercase;margin:6px 10px 0}
.blog-list{left:758px;top:3000px;width:302px}
.blog-item{height:104px;border:1px solid #ddd;border-bottom:3px solid #cfcfcf;padding:14px 8px 0;margin-bottom:0}
.blog-item h4{font-size:14px;font-weight:500;line-height:28px;text-transform:uppercase}
.blog-item .more{margin:0}
.blog-all{left:758px;top:3318px;width:302px;height:59px;background:var(--teal);font-size:16px;border-radius:0}
/* contact */
.contact{left:0;top:3452px;width:1200px;height:800px;background:linear-gradient(180deg,#f5f5f5 0%,#ececec 60%,#e4e4e4 100%)}
.field{height:41px;border:1px solid #bbb;border-radius:3px;background:var(--white);font-size:11px;color:#666;padding:10px 14px}
.contact-btn{left:490px;top:3919px;width:221px;height:49px;background:var(--teal)}
/* footer */
.footer{left:0;top:4128px;width:1200px;height:474px;background:var(--black)}
.foot-logo{left:530px;top:4160px;width:140px;display:flex;flex-direction:column;align-items:center;gap:6px}
.foot-logo .logo-dot{background:var(--white)}
.foot-logo .logo-name{color:var(--white)}
.rule{left:77px;width:1034px;height:1px;background:#444}
.foot-head{font-size:14px;font-weight:700;color:var(--white);text-transform:uppercase}
.foot-list{list-style:none;margin-top:14px}
.foot-list li{font-size:12.5px;color:var(--white);line-height:28px}
.foot-list li::before{content:"»";color:var(--green);margin-right:10px}
.contact-line{display:flex;gap:10px;font-size:12.5px;line-height:28px;color:var(--white);margin-top:8px}
.news{left:839px;top:4370px;width:248px;height:43px;background:var(--white);border-radius:3px;font-size:11px;color:#888;padding:13px 16px}
.social{left:839px;top:4444px;display:flex;gap:14px}
.social span{width:28px;height:28px;border-radius:50%;background:var(--green)}
.copy{left:0;top:4556px;width:1200px;font-size:11px;color:var(--white)}
</style>
</head>
<body>

<header class="site-header abs"></header>
<div class="logo-box abs"><span class="logo-dot"></span><span class="logo-name">QUILL</span></div>
<nav class="nav abs"><span>Home</span><span>About Us</span><span>Services</span><span>Testimonial</span><span>Blog</span><span>Contact Us</span></nav>
<div class="nav-cta btn abs">Book an Appointment</div>

<section>
  <div class="hero abs" role="img" aria-label="Therapist treating a patient's shoulder in a clinic"></div>
  <div class="hero-shade abs"></div>
  <h1 class="hero-title abs center">We Give Solution to Your Pain</h1>
  <p class="hero-text abs center">Lorem ipsum dolor sit amet, consectetur adipiscing elit, sed do eiusmod tempor incididunt ut labore et dolore magna aliqua.<br>Quis ipsum suspendisse ultrices gravida. Risus commodo viverra maecenas accumsan lacus vel facilisis.</p>
  <div class="hero-btn btn abs">Get Started</div>
  <svg class="abs" style="left:0;top:540px" width="1200" height="200" viewBox="0 0 1200 200">
    <defs><linearGradient id="arc" x1="0" x2="1"><stop offset="0" stop-color="#137a78"/><stop offset=".5" stop-color="#79c257"/><stop offset="1" stop-color="#137a78"/></linearGradient></defs>
    <path d="M0 20 Q600 250 1200 20 L1200 200 L0 200 Z" fill="#fff"/>
    <path d="M0 20 Q600 250 1200 20" fill="none" stroke="url(#arc)" stroke-width="10"/>
  </svg>
  <div class="dots abs"><span></span><span></span><span></span><span></span></div>
</section>

<section>
  <h2 class="section-title abs center" style="left:0;top:806px;width:1200px">Our Services
    <svg class="swoosh" width="60" height="14"><path d="M4 3 Q30 16 56 3" fill="none" stroke="#137a78" stroke-width="3"/></svg></h2>
  <p class="para abs center" style="left:210px;top:870px;width:780px">Lorem ipsum dolor sit amet, consectetur adipiscing elit, sed do eiusmod tempor incididunt ut labore et dolore magna aliqua. Quis ipsum sus-pendisse ultrices gravida. Risus commodo viverra maecenas accumsan lacus vel facilisis.</p>

  <div class="card abs" style="left:133px;top:961px"><div class="card-photo" role="img" aria-label="Therapist assessing a man's shoulder" style="background:linear-gradient(160deg,#d9dbe0,#b8a89a)"></div><div class="card-band teal"><span class="card-icon"></span>Lorem Ipsum Dolor Sit</div></div>
  <div class="card abs" style="left:453px;top:961px"><div class="card-photo" role="img" aria-label="Patient doing an arm stretch with a therapist" style="background:linear-gradient(160deg,#e8e8e8,#9aa0a4)"></div><div class="card-band green open"><span class="card-icon"></span>Lorem Ipsum Dolor Sit<p>Lorem ipsum dolor sit amet, consectetur adipi-scing elit, sed do eiusmod tempor incididunt ut labore et dolore magna aliqua.</p></div></div>
  <div class="card abs" style="left:772px;top:961px"><div class="card-photo" role="img" aria-label="Patient on a treatment table with a therapist" style="background:linear-gradient(160deg,#b8bdd8,#5a66a8)"></div><div class="card-band blue"><span class="card-icon"></span>Lorem Ipsum Dolor Sit</div></div>
  <div class="card abs" style="left:133px;top:1324px"><div class="card-photo" role="img" aria-label="Knee rehabilitation exercise on a mat" style="background:linear-gradient(160deg,#eef0ee,#a9c2b4)"></div><div class="card-band teal"><span class="card-icon"></span>Lorem Ipsum Dolor Sit</div></div>
  <div class="card abs" style="left:453px;top:1324px"><div class="card-photo" role="img" aria-label="Close view of hands treating a knee" style="background:linear-gradient(160deg,#c9b1a0,#5b5555)"></div><div class="card-band green"><span class="card-icon"></span>Lorem Ipsum Dolor Sit</div></div>
  <div class="card abs" style="left:772px;top:1324px"><div class="card-photo" role="img" aria-label="Exercise ball session with a therapist" style="background:linear-gradient(160deg,#9a9a9a,#5d6a6a)"></div><div class="card-band blue"><span class="card-icon"></span>Lorem Ipsum Dolor Sit</div></div>
</section>

<section>
  <div class="about abs"></div>
  <svg class="abs" style="left:548px;top:1745px" width="640" height="610" viewBox="0 0 640 610">
    <circle cx="316" cy="324" r="322" fill="none" stroke="#ffffff" stroke-opacity=".35" stroke-width="8"/>
    <circle cx="316" cy="324" r="296" fill="#5f8f9a" role="img" aria-label="Therapist guiding a patient on an exercise ball"/>
    <circle cx="316" cy="324" r="34" fill="#79c257"/>
    <path d="M306 308 L332 324 L306 340 Z" fill="#fff"/>
  </svg>
  <h2 class="about-title abs">About<br>Quill Physical Therapy
    <svg style="display:block;margin-top:2px" width="70" height="14"><path d="M4 3 Q35 16 66 3" fill="none" stroke="#fff" stroke-width="3"/></svg></h2>
  <p class="about-text abs">Lorem ipsum dolor sit amet, consectetur adipiscing elit, sed do eiusmod tempor incididunt ut labore et dolore magna aliqua. Quis ipsum suspendisse ultrices gravida. Risus commodo viverra maecenas accumsan lacus vel facilisis. Sed ut perspiciatis unde omnis iste natus error sit voluptatem accusantium doloremque laudantium, totam rem aperiam, eaque ipsa quae ab illo inventore veritatis et quasi architecto beatae vitae dicta sunt explicabo. Nemo enim ipsam voluptatem quia voluptas sit aspernatur aut odit aut fugit, sed quia consequuntur magni dolores eos.</p>
  <div class="about-btn btn abs">Learn More</div>
</section>

<section>
  <div class="testimonials abs"></div>
  <h2 class="testi-title abs center">OUR CLIENT TESTIMONIALS
    <svg class="swoosh" width="60" height="14"><path d="M4 3 Q30 16 56 3" fill="none" stroke="#fff" stroke-width="3"/></svg></h2>
  <p class="testi-text abs center"><b style="font-size:20px">“</b> Lorem ipsum dolor sit amet, consectetur adipiscing elit, sed do eiusmod tempor incididunt ut labore et dolore magna aliqua. Quis ipsum sus-pendisse ultrices gravida. Risus commodo viverra maecenas accumsan lacus vel facilisis. Sed ut perspiciatis unde omnis iste natus error sit voluptatem accusantium doloremque laudantium, totam rem aperiam, eaque ipsa quae ab illo inventore veritatis et quasi architecto beatae vitae dicta sunt explicabo. Nemo enim ipsam voluptatem quia voluptas sit aspernatur aut odit aut fugit, sed quia consequuntur magni dolores eos.es accumsan lacus vel facilisis sed ut perspiciatis unde omnis iste natus error sit voluptatem accusantium. <b style="font-size:20px">”</b></p>
  <p class="testi-name abs center">John Deo</p>
  <div class="arrow abs" style="left:108px;top:2572px"><svg width="14" height="14"><path d="M10 1 L4 7 L10 13" fill="none" stroke="#137a78" stroke-width="2"/></svg></div>
  <div class="arrow abs" style="left:1038px;top:2572px"><svg width="14" height="14"><path d="M4 1 L10 7 L4 13" fill="none" stroke="#137a78" stroke-width="2"/></svg></div>
</section>

<section>
  <h2 class="section-title abs center" style="left:0;top:2854px;width:1200px">Our Latest Blog
    <svg class="swoosh" width="60" height="14"><path d="M4 3 Q30 16 56 3" fill="none" stroke="#137a78" stroke-width="3"/></svg></h2>
  <p class="para abs center" style="left:210px;top:2920px;width:780px">Lorem ipsum dolor sit amet, consectetur adipiscing elit, sed do eiusmod tempor incididunt ut labore et dolore magna aliqua. Quis ipsum sus-pendisse ultrices gravida. Risus commodo viverra maecenas accumsan lacus vel facilisis.</p>

  <article class="blog-card abs" style="left:140px;top:3000px"><div class="blog-photo" role="img" aria-label="Therapist examining a patient's arm" style="background:linear-gradient(160deg,#e9e6e2,#a9b3b8)"></div><h3>Lorem Ipsum Dolor Sit Ameto Nsectetur Adipiscing Eli.</h3><p>Lorem ipsum dolor sit amet, consectetur adipi-scing elit, sed do eiusmod tempor incididunt ut labore et dolore magna aliqua.</p><span class="more">Learn More</span></article>
  <article class="blog-card abs" style="left:451px;top:3000px"><div class="blog-photo" role="img" aria-label="Women exercising on mats in a studio" style="background:linear-gradient(160deg,#d6cfd3,#6a6f78)"></div><h3>Lorem Ipsum Dolor Sit Ameto Nsectetur Adipiscing Eli.</h3><p>Lorem ipsum dolor sit amet, consectetur adipi-scing elit, sed do eiusmod tempor incididunt ut labore et dolore magna aliqua.</p><span class="more">Learn More</span></article>

  <div class="blog-list abs">
    <div class="blog-item"><h4>Lorem Ipsum Dolor Sit Ameto Nsectetur Adipiscing Eli.</h4><span class="more">Learn More</span></div>
    <div class="blog-item"><h4>Lorem Ipsum Dolor Sit Ameto Nsectetur Adipiscing Eli.</h4><span class="more">Learn More</span></div>
    <div class="blog-item"><h4>Lorem Ipsum Dolor Sit Ameto Nsectetur Adipiscing Eli.</h4><span class="more">Learn More</span></div>
  </div>
  <div class="blog-all btn abs">View All Blogs</div>
</section>

<section>
  <div class="contact abs"></div>
  <h2 class="section-title abs center" style="left:0;top:3526px;width:1200px">Get in Touch
    <svg class="swoosh" width="60" height="14"><path d="M4 3 Q30 16 56 3" fill="none" stroke="#137a78" stroke-width="3"/></svg></h2>
  <p class="para abs center" style="left:210px;top:3592px;width:780px">Lorem ipsum dolor sit amet, consectetur adipiscing elit, sed do eiusmod tempor incididunt ut labore et dolore magna aliqua. Quis ipsum sus-pendisse ultrices gravida. Risus commodo viverra maecenas accumsan lacus vel facilisis.</p>
  <div class="field abs" style="left:228px;top:3666px;width:365px">First name</div>
  <div class="field abs" style="left:605px;top:3666px;width:365px">Last name</div>
  <div class="field abs" style="left:228px;top:3722px;width:365px">Email</div>
  <div class="field abs" style="left:605px;top:3722px;width:365px">Phone</div>
  <div class="field abs" style="left:228px;top:3779px;width:742px;height:102px">Message</div>
  <div class="contact-btn btn abs">Book an Appointment</div>
</section>

<footer>
  <svg class="abs" style="left:0;top:4030px" width="1200" height="110" viewBox="0 0 1200 110">
    <defs><linearGradient id="farc" x1="0" x2="1"><stop offset="0" stop-color="#137a78"/><stop offset=".5" stop-color="#79c257"/><stop offset="1" stop-color="#137a78"/></linearGradient></defs>
    <path d="M0 180 Q600 -60 1200 180 L1200 110 L0 110 Z" fill="#0b0b0b"/>
    <path d="M0 180 Q600 -60 1200 180" fill="none" stroke="url(#farc)" stroke-width="12"/>
  </svg>
  <div class="footer abs"></div>
  <div class="foot-logo abs"><span class="logo-dot"></span><span class="logo-name">QUILL</span></div>
  <div class="rule abs" style="top:4298px"></div>

  <div class="abs" style="left:113px;top:4335px"><h4 class="foot-head">Quick Links</h4><ul class="foot-list"><li>Home</li><li>About Us</li><li>Services</li><li>Testimonial</li><li>Blog</li></ul></div>
  <div class="abs" style="left:327px;top:4335px"><h4 class="foot-head">Legal</h4><ul class="foot-list"><li>Terms of Use</li><li>Privacy Policy</li><li>Contact Us</li><li>FAQ</li></ul></div>
  <div class="abs" style="left:535px;top:4335px;width:270px"><h4 class="foot-head">Contact Us</h4>
    <div class="contact-line"><svg width="12" height="16" style="margin-top:6px;flex:none"><path d="M6 1a5 5 0 0 1 5 5c0 4-5 9-5 9S1 10 1 6a5 5 0 0 1 5-5z" fill="#79c257"/><circle cx="6" cy="6" r="2" fill="#0b0b0b"/></svg><span>123 Sed ut perspiciatis unde omnis iste natus error sit voluptatem</span></div>
    <div class="contact-line"><svg width="14" height="14" style="margin-top:7px;flex:none"><path d="M3 1l3 3-2 2c1 2 2 3 4 4l2-2 3 3-2 2C6 13 1 8 1 3z" fill="#79c257"/></svg><span>123 456 7890</span></div>
    <div class="contact-line"><svg width="14" height="12" style="margin-top:8px;flex:none"><rect width="14" height="10" fill="#79c257"/><path d="M0 0l7 6 7-6" fill="none" stroke="#0b0b0b"/></svg><span>info@quillphysicaltherapy.com</span></div>
  </div>
  <div class="abs" style="left:839px;top:4335px"><h4 class="foot-head">Subscribe the Newsletters</h4></div>
  <div class="news abs">Enter The Email
    <svg class="abs" style="right:14px;top:13px" width="16" height="16"><path d="M1 8 L15 1 L11 15 L8 9 Z" fill="#79c257"/></svg></div>
  <div class="social abs"><span></span><span></span><span></span><span></span></div>
  <div class="rule abs" style="top:4535px"></div>
  <p class="copy abs center">© Copyrights 2021 Quill Physical Therapy &nbsp;|&nbsp; All Rights Reserved</p>
</footer>

</body>
</html>
```